Digital Imaging Website Design Project

This project is for 3 page designs - The main Home page design, department page design & content page design which will utilize most of the home page components.

Client Background - http://www.klmvxco.example

An almost Forty year old established printing company that has a large client base of architect/engineering, as the print shop opened up as a blueprinting company, and over the years has grown, changed and expanded to offer document and digital file management for this industry. KLMVxco. has also always offered color printing services, but recently has expanded their color department to be able to offer amazing dimensional printing, and extreme cutting technology.

These new products and services will be targeted to new industries for repeatable printing needs, promotional, point of purchase color printing, as well as in-store, interior decor/wall. These new printing services are only offered by KLMVXCO in their area, and they want to convey that they are on the leading edge of color printing technology, while at the same time, not eliminating their existing primary business scaring away their traditional client base of architectural/engineering firms that use them for large format printing, scanning and document management services.

1 - Home Page Design
Primary Goals of the design:

1.Provide a new, eye catching engaging website that conveys the above expansion/growth/cutting edge company.
2.Full screen design please to move away from the 'center' bordered up website they currently have.
3.Design Components – We don't have any media to provide you with exception of our logo. We're looking for fresh design that is exciting and engaging imagery. Additionally, we are working on a color/effected version of our logo to place on the color division page, and this will probably tie in with the design you create for us.
4.It should be designed to be able to work as a responsive design as well so that when installed, will work across devices etc..
5.Colors – Same color scheme, but if you have an accent color you'd like to use to make the site pop, go for it!

Requirements:
1.The 4 divisions of the company should be the main feature so that the client depending on which department they are needing, will see those 4 choices clearly in the design, and they'll know to click on one of them to get more information and to their needed services.

2.The main goal of the site is to get visitors to place an order, there should be a feature on the home page for this call to action.

3.Put in an element that communicates the main benefit of KLMVxco. - an area for a 1-line Statement/Call to Action / Overall Company Benefit/

4.The 4 divisions need to have eye catching elements related to their products and services, and that clearly illustrate that the user should click on that to go to the appropriate area for products and services

Reprographics
This department is specifically geared to architect/engineering industry
BYLine for optional Use: Partnering with Building Industry Providers since 1975
Related pages for better understanding:
http://www.klmvxco.example/services/portland_professional_printing_services
http://www.klmvxco.example/services/reprographics
Digital File Management
This department is related to Architect/engineers, but can also apply to any other industry needing electronic document management, scanning, or archival services.
BYLine for optional use: Effective & Efficient Digital Solutions at every level.
Related Pages:
http://www.klmvxco.example/colorgraphics/electronic_file_document_management
http://www.klmvxco.example/colorgraphics/document_scanning_service
http://www.klmvxco.example/services/scanning_and_archiving

Color Graphics
This Department is newly expanded / has expanded services / they are focusing more of their efforts on this department and is a key reason for updated website design.
This Department image/representation should be stellar in the imagery to convey the excellence of the color department the services availble.
One of their newest products/services is dimensional printing – not 3-D, but raised element printing. Essentially a client could pick components on their graphic that that they want to 'bump' out, and additional layers would be put in place to create a popped out, dimensional effect. * Bonus points for creating the color department image that effectively conveys this new service – whether it's showing an abstract image/element that is actually raised off the page/paper/component. Additionally the color dimensional printing can be done on practically any material – glass, vinyl, material etc.... Please let me know if you have any questions on this.
BYLine for optional Use: See How Our Color Stands Out From the Rest
Related pages:
http://www.klmvxco.example/colorgraphics
http://www.klmvxco.example/colorgraphics/color_digital_imaging

Equipment & Supplies
This department provides specific supplies and hardware vs. printing products/services. Our largest client base is architects/engineers, but is not limited to this industry. Typical equipment is large printers, and supplies are typically paper products geared to the large format printing services, for the architect/engineers industry.
Byline for optional Use: In-House Printing & Fulfillment Services
Related pages:
http://www.klmvxco.example/tarvo_ulix_equipment_sales
http://www.klmvxco.example/supplies

Additionally - Possibly have descriptive text sections below these 4 elements, but this is optional.

2.) Department/Division Page design -

This page should pull the home page element to over based on which division is selected.
Have a submenu design incorporated so that users can navigate to all the products and services that will be listed under that division
Contain a plugin design for FAQs – so that depending on which division page they are on, the appropriate FAQ's would display for use to have easy access to.
Contain a plugin design for – Contact Us easy form – short form –
Name
Company
Number
Email
Project Details/Questions: Text box

3.)Content Page design
This page should have main area for content
Area for an image with slideshow of other supporting images
Optional area for video – most (99%) of the pages will not have videos, but in the case we do, would like an area that will display videos effectively.
Optional FAQ plugin display
Contact plugin display

Global Elements:

Static and very visible site features that are in a position so that if user clicks beyond home page will still see these are:
Get a Quote
Place Order
Digital Plan-room
Call Today - 555-384-7290

Other global components:
SM Icons – QN, Chirpa, Workrung
Rotating Testimonial

Navigational Menu:
The KVZ Difference
About
Sustainability
Products & Services
Reprograhics
Digital File Management
Color Graphics
Equipment & Supplies
Login
Blog
Contact Us

After the contest – What would be great to have is when a user clicks on one of the departments, it takes that visual element and continues onto it's department page for a smaller but related image - But this may be an after this web design contest.

Additionally will need some other design work on the interior pages, as well, so hoping to find a great designer to complete the other tasks – as well as be the go-to for future endeavors!

Thanks for looking at the project, and I look forward to any questions you may have.
Updates

Looking forward to hearing from interested designers! - If you're curious about my work, you can find my profile at:  https://www.jobrilly.example/users/~07f3b92e61cd5a0b48

Target Market(s)

Please see description

Industry/Entity Type

Electronic

Requirements
Must have
• Please see description

```html
<!DOCTYPE html>
<html lang="en">
<head>
<meta charset="utf-8">
<title>KVZ Digital Imaging</title>
<link rel="stylesheet" href="https://fonts.googleapis.com/css2?family=Ubuntu:ital,wght@0,300;0,400;0,500;0,700;1,300&display=swap">
<style>
:root{
  --navy:#0d2a7a;
  --blue:#1a3f9e;
  --ink:#333;
  --link:#1f4aa8;
  --hero-bg:#f4f4ef;
  --white:#fff;
}
*{box-sizing:border-box;margin:0;padding:0}
html,body{width:1074px;height:1200px;overflow:hidden}
body{font-family:"Ubuntu",sans-serif;font-weight:300;color:var(--ink);background:var(--white);position:relative}
a{color:inherit;text-decoration:none}

.site-header{position:absolute;left:0;top:0;width:1074px;height:125px;border-top:4px solid #c9d6ec;background:var(--white)}
.brand{position:absolute;left:60px;top:30px;display:flex;align-items:center;gap:12px}
.brand-dot{width:58px;height:58px;border-radius:50%;background:var(--navy)}
.brand-name{font-weight:700;color:var(--navy);font-size:16px;line-height:18px;letter-spacing:.3px}
.brand-tag{font-size:10.5px;color:var(--navy);font-weight:400;margin-top:6px}
.call{position:absolute;left:543px;top:16px;font-size:17px;color:#333;display:flex;align-items:center;gap:5px;white-space:nowrap}
.call strong{font-weight:500;color:var(--navy);font-size:20px;margin-left:4px}
.utility{position:absolute;left:795px;top:19px;font-size:13px;color:var(--link);font-weight:400;white-space:nowrap}
.utility span{margin:0 5px;color:#555}
.actions{position:absolute;left:607px;top:80px;display:flex;gap:10px}
.action-btn{height:32px;padding:0 10px;border:1px solid #c8c8c8;border-radius:3px;background:linear-gradient(#fff,#e9e9e9);display:flex;align-items:center;gap:7px;font-size:14px;color:#222;font-weight:400}

.main-nav{position:absolute;left:0;top:125px;width:1074px;height:50px;background:linear-gradient(#2a5cc0,#123a94);display:flex;padding-left:46px}
.main-nav a{color:var(--white);font-size:17.5px;font-weight:400;padding:0 21px;line-height:50px;border-right:1px solid rgba(255,255,255,.2)}

.divisions{position:absolute;left:0;top:175px;width:1074px;height:361px;background:var(--hero-bg);border-bottom:1px solid #e2e2dc}
.tile{position:absolute;top:18px;width:232px;height:305px;overflow:hidden;border-radius:2px}
.tile-image{width:100%;height:236px}
.tile-caption{position:absolute;left:0;bottom:0;width:100%;height:71px;background:linear-gradient(#1f4fb2,#0b236c);color:var(--white);padding:16px 0 0 17px}
.tile-caption h3{font-weight:300;font-size:19px}
.tile-caption small{display:block;font-size:10.5px;font-weight:500;margin-top:4px;letter-spacing:.2px}

.content{position:absolute;left:0;top:536px;width:1074px;height:325px}
.section-title{font-weight:400;font-size:24px;color:var(--navy)}
.about{position:absolute;left:59px;top:48px;width:356px}
.about-photo{float:left;width:122px;height:115px;border-radius:10px;background:linear-gradient(135deg,#6d7c8c,#c7ced6 45%,#d8536a 75%,#3ea0d8);margin:15px 14px 4px 0}
.about p{font-size:12.5px;line-height:22.6px;color:var(--link);padding-top:10px}
.read-more{display:inline-block;margin-top:5px;background:linear-gradient(#1d3f95,#0b1f62);color:#fff;font-size:10.5px;font-weight:500;padding:7px 14px;border-radius:2px}
.news{position:absolute;left:457px;top:38px;width:280px}
.news-title{font-weight:400;font-size:24px;color:#222}
.news-item{font-size:12.5px;line-height:22.5px;color:#444;margin-top:19px}
.news-item:first-of-type{margin-top:12px}
.news-item b{font-weight:500}
.cta{position:absolute;left:770px;width:247px;border-radius:3px;color:#fff;padding:12px 0 0 24px;display:flex;gap:8px}
.cta h4{font-weight:400;font-size:20px}
.cta p{font-size:11px;opacity:.8;margin-top:4px}
.cta-quote{top:26px;height:72px;background:linear-gradient(#2d5fc6,#0f2e82)}
.cta-order{top:104px;height:72px;background:linear-gradient(#ffa21c,#ff7b00)}
.cta-plan{top:184px;height:79px;background:linear-gradient(#97c93a,#5f9a12);padding-top:16px}

.site-footer{position:absolute;left:0;top:861px;width:1074px;height:339px;background:linear-gradient(#2456b8,#0f2c86 70%,#0c2578);color:var(--white)}
.footer-title{font-weight:400;font-size:21px}
.footer-col{position:absolute;top:34px}
.footer-col ul{list-style:none;margin-top:11px}
.footer-col li{font-size:13px;line-height:27.3px;font-weight:300}
.testimonial{position:absolute;left:445px;top:24px;width:284px;height:197px;background:linear-gradient(#213f99,#0d236b);border-radius:4px;box-shadow:0 0 6px rgba(0,0,0,.3);padding:17px 22px 0 30px}
.testimonial p{font-style:italic;font-size:11.5px;line-height:19.3px;margin-top:8px;opacity:.9;letter-spacing:-.1px}
.testimonial cite{display:block;font-style:normal;font-weight:400;font-size:12.5px;margin-top:5px}
.testimonial-arrows{position:absolute;right:22px;bottom:20px}
.social{display:flex;gap:6px;margin-top:12px}
.social span{width:29px;height:29px;border-radius:50%;background:#fff;border:2px solid #a9bde6}
.social-names{font-size:13px;margin-top:12px;font-weight:300}
.footer-rule{position:absolute;left:86px;top:270px;width:904px;border-top:1px solid rgba(255,255,255,.25)}
.copyright{position:absolute;left:90px;top:290px;font-size:12.5px;color:#a9b6da}
</style>
</head>
<body>

<header class="site-header">
  <div class="brand">
    <span class="brand-dot"></span>
    <div>
      <div class="brand-name">KORVANE VELLUM<br>&amp; ZINCPRINT CO.</div>
      <div class="brand-tag">Client-Driven Service Since 1975</div>
    </div>
  </div>
  <div class="call">
    <svg width="20" height="16" viewBox="0 0 20 16"><path d="M2 6c0-3 16-3 16 0v2h-4V6c-2-1-6-1-8 0v2H2z" fill="#222"/><rect x="5" y="8" width="10" height="7" rx="1" fill="#222"/></svg>
    Call Today <strong>555-384-7290</strong>
  </div>
  <nav class="utility"><a href="#">About</a><span>|</span><a href="#">Login</a><span>|</span><a href="#">Blog</a><span>|</span><a href="#">Contact Us</a></nav>
  <div class="actions">
    <a class="action-btn" href="#"><svg width="22" height="16" viewBox="0 0 22 16"><path d="M3 2h16a2 2 0 0 1 2 2v5a2 2 0 0 1-2 2H9l-5 4v-4H3a2 2 0 0 1-2-2V4a2 2 0 0 1 2-2z" fill="none" stroke="#111" stroke-width="2.2"/></svg>Get a Quote</a>
    <a class="action-btn" href="#"><svg width="22" height="18" viewBox="0 0 22 18"><path d="M1 2h3l3 10h11l2-7H6" fill="none" stroke="#111" stroke-width="1.8"/><circle cx="9" cy="15" r="1.6" fill="#111"/><circle cx="16" cy="15" r="1.6" fill="#111"/></svg>Place Order</a>
    <a class="action-btn" href="#"><svg width="20" height="18" viewBox="0 0 20 18"><path d="M10 1l8 4v8l-8 4-8-4V5z" fill="none" stroke="#333" stroke-width="1.5"/></svg>Digital Planroom</a>
  </div>
</header>

<nav class="main-nav">
  <a href="#">The KVZ Difference</a><a href="#">Products &amp; Services</a><a href="#">Login</a><a href="#">About</a><a href="#">Contact Us</a>
</nav>

<section class="divisions">
  <a class="tile" href="#" style="left:56px">
    <div class="tile-image" role="img" aria-label="Rolled blueprints with a pencil and drafting triangle" style="background:linear-gradient(135deg,#e9edf2,#c9d6e2 60%,#8fb3d6)"></div>
    <div class="tile-caption"><h3>Reprographics</h3><small>MORE INFO</small></div>
  </a>
  <a class="tile" href="#" style="left:297px">
    <div class="tile-image" role="img" aria-label="Person working at a computer keyboard" style="background:linear-gradient(135deg,#5a4636,#c9b9a4 40%,#ebe7e0 70%,#8a7766)"></div>
    <div class="tile-caption"><h3>Digital File Management</h3><small>MORE INFO</small></div>
  </a>
  <a class="tile" href="#" style="left:539px">
    <div class="tile-image" role="img" aria-label="Fanned colour swatch guide" style="background:linear-gradient(120deg,#1aa0e0,#26c4b8 25%,#f4e12a 45%,#f28a1c 62%,#e2237a 80%,#7d3ab0)"></div>
    <div class="tile-caption"><h3>Color Graphics</h3><small>MORE INFO</small></div>
  </a>
  <a class="tile" href="#" style="left:780px">
    <div class="tile-image" role="img" aria-label="Large format printing equipment in a print shop" style="background:linear-gradient(#dfe6ee,#a9b6c4 50%,#6f8fb8)"></div>
    <div class="tile-caption"><h3>Equipment &amp; Supplies</h3><small>MORE INFO</small></div>
  </a>
</section>

<main class="content">
  <div class="about">
    <h2 class="section-title">About Our Company</h2>
    <div class="about-photo" role="img" aria-label="Printing press operator checking colour output"></div>
    <p>Founded in 1975 by Daniel Orrick, Korvane Vellum &amp; Zincprint (KVZ) is a full service reprographics company serving Oregon and Southwest Wash-ington's design and building community.&nbsp; We utilize the latest digital technologies to provide a wide range of reprographics and graphic imaging</p>
    <a class="read-more" href="#">READ MORE</a>
  </div>

  <div class="news">
    <h2 class="news-title">Recent News</h2>
    <p class="news-item"><b>07/10/2013</b> Phasellus felis dolor, scelerisque a, tempus eget, lobortis id, libero.</p>
    <p class="news-item"><b>06/10/2013</b> Donec scelerisque leo ac risus.</p>
    <p class="news-item"><b>05/10/2013</b> Praesent sit amet est. In dictum, dolor eu dictum porttitor enim felis viverra</p>
  </div>

  <a class="cta cta-quote" href="#">
    <svg width="32" height="30" viewBox="0 0 32 30"><path d="M16 2C8 2 2 7 2 13c0 4 2 7 6 9l-1 6 6-4h3c8 0 14-5 14-11S24 2 16 2z" fill="#fff"/><path d="M10 10h4v4l-2 4M18 10h4v4l-2 4" stroke="#1f4aa8" stroke-width="2.4" fill="none"/></svg>
    <div><h4>Get a Quote</h4><p>Nunc tempus felis vitae urna</p></div>
  </a>
  <a class="cta cta-order" href="#">
    <svg width="36" height="32" viewBox="0 0 36 32"><path d="M2 4h5l4 16h18l4-11H9" fill="none" stroke="#fff" stroke-width="2.4"/><path d="M13 13h17M14 16h14" stroke="#fff" stroke-width="1.5"/><circle cx="14" cy="26" r="2.4" fill="#fff"/><circle cx="27" cy="26" r="2.4" fill="#fff"/></svg>
    <div><h4>Place Order</h4><p>Vivamus porttitor g purus nisi</p></div>
  </a>
  <a class="cta cta-plan" href="#">
    <svg width="36" height="30" viewBox="0 0 36 30"><ellipse cx="18" cy="14" rx="14" ry="11" fill="none" stroke="#fff" stroke-width="2.2"/><path d="M4 14h28M18 3v22M8 7c6 3 14 3 20 0M8 21c6-3 14-3 20 0" stroke="#fff" stroke-width="1.5" fill="none"/></svg>
    <div><h4>Digital Plan-room</h4><p>Nunc tempus felis vitae urna</p></div>
  </a>
</main>

<footer class="site-footer">
  <div class="footer-col" style="left:65px">
    <h3 class="footer-title">Quick Links</h3>
    <ul><li>The KVZ Difference</li><li>About</li><li>Sustainability</li><li>Products &amp; Services</li><li>Reprograhics</li><li>Digital File Management</li></ul>
  </div>
  <div class="footer-col" style="left:264px">
    <h3 class="footer-title">Sublinks</h3>
    <ul><li>Color Graphics</li><li>Equipment &amp; Supplies</li><li>Login</li><li>Blog</li><li>Contact Us</li></ul>
  </div>
  <blockquote class="testimonial">
    <h3 class="footer-title" style="font-size:22px">Testimonials</h3>
    <p>Phasellus felis dolor, scelerisque a, tempus eget, lobortis id, libero. Donec scelerisque leo ac risus. Praesent sit amet est. In dictum, dolor eu dictum porttitor, enim felis viverra mi, eget luctus massa purus quis odio.</p>
    <cite>By Author Name</cite>
    <svg class="testimonial-arrows" width="30" height="20" viewBox="0 0 30 20"><path d="M10 2L3 10l7 8M20 2l7 8-7 8" stroke="#fff" stroke-width="2" fill="none"/></svg>
  </blockquote>
  <div class="footer-col" style="left:793px">
    <h3 class="footer-title">Get Connected</h3>
    <div class="social"><span></span><span></span><span></span></div>
    <p class="social-names">QN &nbsp;/ Chirpa / Workrung</p>
  </div>
  <div class="footer-rule"></div>
  <p class="copyright">© 2013 Company Name.&nbsp; All right reserved.&nbsp; Term of Use</p>
</footer>

</body>
</html>
```